Pine Ridge Electrical winter special

I need an ad for a print magazine for my electrical contracting business.
It must have my logo and business name as the main back ground with a banner over the top stating 'winter solar special 10% off'
it must have my licence number in the botomm right corner lic.472915D
It must have my name Martin Delacey ph 0482139756
Also I would like it to say somewher 'Call now for your free solar assessment'
I would like it on a sharp black bagground like my business card attached and flyer attached
This will be a in a landscape design not potrait
Target Market(s)
Print ad and banner advertising
Industry/Entity Type
Solar Energy
Colors
Designer to choose colors to be used in the design.
Requirements
Must have
- my licence number on bottom right corner
- lic.472915D

```html
<!DOCTYPE html>
<html lang="en">
<head>
<meta charset="utf-8">
<title>Pine Ridge Electrical – Winter Solar Special</title>
<link href="https://fonts.googleapis.com/css2?family=Archivo+Black&family=Barlow:wght@400;500&family=Michroma&family=Orbitron:wght@800;900&display=swap" rel="stylesheet">
<style>
  :root {
    --page: #ffffff;
    --ink-black: #060606;
    --deep-blue: #1f3c8f;
    --brand-blue: #2a67b0;
    --sky-blue: #29abe2;
    --free-blue: #2ba6e0;
    --silver-light: #eeeff1;
    --silver-mid: #c3c5c9;
    --snow: #f4f8fb;
    --white: #ffffff;
    --text-dark: #111111;
    --muted: #3a3a3a;
  }
  * { margin: 0; padding: 0; box-sizing: border-box; }
  html, body {
    width: 982px; height: 1200px; overflow: hidden;
    background: var(--page);
  }
  .ad {
    position: absolute; left: 38px; top: 46px;
    width: 908px; height: 454px; overflow: hidden;
    background: linear-gradient(180deg, var(--silver-light) 40%, var(--silver-mid) 100%);
  }
  .ad-backdrop { position: absolute; inset: 0; }
  .brand-mark {
    position: absolute; left: 152px; top: 50px;
    width: 96px; height: 96px; border-radius: 50%;
    background: var(--brand-blue);
  }
  .brand-name {
    position: absolute; left: 30px; width: 440px; top: 172px;
    text-align: center;
    font-family: "Michroma", sans-serif; font-size: 40px; line-height: 1;
    color: var(--brand-blue); letter-spacing: 0.5px;
  }
  .brand-trade {
    position: absolute; left: 30px; width: 440px; top: 222px;
    text-align: center;
    font-family: "Michroma", sans-serif; font-size: 15px;
    letter-spacing: 9px; color: var(--brand-blue);
  }
  .cta-lead, .cta-tail {
    position: absolute; left: 130px; width: 260px; text-align: center;
    font-family: "Archivo Black", sans-serif; color: var(--white);
  }
  .cta-lead { top: 244px; font-size: 17px; }
  .cta-free {
    position: absolute; left: 120px; width: 280px; top: 258px; text-align: center;
    font-family: "Orbitron", sans-serif; font-weight: 900; font-size: 58px;
    line-height: 1; color: var(--free-blue); letter-spacing: 2px;
  }
  .cta-tail { top: 314px; font-size: 14.5px; }
  .phone {
    position: absolute; left: 52px; top: 360px;
    font-family: "Orbitron", sans-serif; font-weight: 900; font-size: 64px;
    line-height: 1; color: var(--ink-black); letter-spacing: 3px;
  }
  .contact-line {
    position: absolute; left: 54px; top: 416px;
    font-family: "Archivo Black", sans-serif; font-size: 14.5px;
    color: var(--text-dark);
  }
  .contact-line .divider { color: var(--muted); margin: 0 8px; font-family: "Barlow", sans-serif; }
  .licence {
    position: absolute; right: 36px; top: 418px;
    font-family: "Barlow", sans-serif; font-weight: 500; font-size: 14px;
    color: var(--muted); letter-spacing: 0.5px;
  }
  .snowflake-spot {
    position: absolute; left: 684px; top: 370px; width: 70px; height: 70px;
    border-radius: 50%;
    background: radial-gradient(circle, rgba(255,255,255,0.85) 0%, rgba(255,255,255,0) 70%);
  }
  .promo-seal { position: absolute; left: 556px; top: 39px; width: 320px; height: 320px; }
</style>
</head>
<body>
  <section class="ad" aria-label="Pine Ridge Electrical winter solar special advertisement">
    <svg class="ad-backdrop" width="908" height="454" viewBox="0 0 908 454" aria-hidden="true">
      <path d="M0,0 H908 V205 C880,205 860,206 830,212 C700,238 380,338 200,350 C130,348 60,322 0,289 Z" fill="var(--ink-black)"/>
      <path d="M0,289 C60,322 130,348 200,350 C330,344 470,300 600,262" fill="none" stroke="var(--deep-blue)" stroke-width="6"/>
      <path d="M760,250 C810,214 870,204 908,205 V300 C860,296 800,280 760,250 Z" fill="var(--snow)"/>
    </svg>

    <div class="brand-mark" aria-hidden="true"></div>
    <div class="brand-name">PINE RIDGE</div>
    <div class="brand-trade">ELECTRICAL</div>

    <p class="cta-lead">CALL NOW FOR YOUR</p>
    <p class="cta-free">FREE</p>
    <p class="cta-tail">SOLAR ASSESSMENT</p>

    <p class="phone">0482139756</p>
    <p class="contact-line">www.pineridgeelectrical.com<span class="divider">|</span>info@pineridgeelectrical.com.au</p>
    <p class="licence">lic.472915D</p>

    <div class="snowflake-spot" role="img" aria-label="Snowflake decoration"></div>

    <svg class="promo-seal" viewBox="0 0 320 320" aria-label="Winter solar special, 10% off">
      <defs>
        <path id="seal-top" d="M42,160 A118,118 0 0 1 278,160"/>
        <path id="seal-bottom" d="M30,160 A130,130 0 0 0 290,160"/>
      </defs>
      <circle cx="160" cy="160" r="154" fill="var(--deep-blue)"/>
      <circle cx="160" cy="160" r="145" fill="var(--silver-light)"/>
      <circle cx="160" cy="160" r="96" fill="none" stroke="var(--deep-blue)" stroke-width="4"/>
      <circle cx="160" cy="160" r="90" fill="var(--sky-blue)"/>
      <text font-family="Archivo Black, sans-serif" font-size="34" fill="var(--deep-blue)" letter-spacing="1">
        <textPath href="#seal-top" startOffset="50%" text-anchor="middle">WINTER SOLAR</textPath>
      </text>
      <text font-family="Archivo Black, sans-serif" font-size="40" fill="var(--deep-blue)" letter-spacing="2" dominant-baseline="hanging">
        <textPath href="#seal-bottom" startOffset="50%" text-anchor="middle">SPECIAL</textPath>
      </text>
      <polygon points="42,184 46,194 56,194 48,200 51,210 42,204 33,210 36,200 28,194 38,194" fill="var(--deep-blue)"/>
      <polygon points="278,184 282,194 292,194 284,200 287,210 278,204 269,210 272,200 264,194 274,194" fill="var(--deep-blue)"/>
      <text x="160" y="150" text-anchor="middle" font-family="Orbitron, sans-serif" font-weight="900" font-size="52" fill="var(--white)">10%</text>
      <text x="160" y="210" text-anchor="middle" font-family="Orbitron, sans-serif" font-weight="900" font-size="54" fill="var(--white)">OFF</text>
    </svg>
  </section>
</body>
</html>
```